Probate (Legal) Wordpress Design with Coding for Online Company

I need a Wordpress design with coding, pictures, content to be provided by me, fully responsive, and development. This is for a 6-7 page design.

Pages Needed: Home/About/Probate/Process/FAQ/Contact Us/Blog.

The home page should be organized as followed:
-Steps in Probate: Gather; Implement; Close (each step will come with content)
-Flat-Fee Price & Savings: Content will go here with a button to contact us (phone number) or just the phone number.
-You Have Questions, We Have Answers: five questions with content. Only one question answer to show at a time when clicked on the question from the list.
-Get to Know Us: a brief description with content about what we do and who we are.

Main image slogan: Helping Californians deal with loss with DIGNITY & UNDERSTATING (you may use a better slogan if you wish).

The Contact page should not have a map since we are an online company. We service the entire state of California in every county and city.

The About page should be simple, direct, and easy on the eye. It should have a brief description of who we are and it should have no more than 6 reasons why the client should hire us.

About our online California company. We are not attorneys but legal document assistants who prepare legal documents for probate estate when someone dies with or without a will and assets need to be distributed. We have a flat-fee for Formal Probate of $999 and $699 for Informal Probate. We are an online company and offer our services to the entire state of California in every county. We do everything over the phone and email. The turn around time for us to prepare the initial legal paperwork for the client is within 3-5 business days. We can prepare, file, serve and manage a probate matter from petition to closing. We are not attorneys so our prices are very affordable compare to the attorney.

The company name for the website will be www.velmarhollow.com, The Velmar Hollow Group.

I do not have a logo yet. The colors of the website should be easy on the eye and calming. THE SITE SHOULD BE SIMPLE AND STRAIGHT TO THE POINT. EASY TO NAVIGATE.

The company phone number should be very visible and should stand out to the client. It should also be clickable and ready to dial for smartphone users.

I do not want a contact form on the homepage. THE MAIN THING IS FOR THE POTENTIAL CLIENT TO CALL OUR OFFICE TO SIGN UP.

I do like some images of family or people since we are dealing with people who just lost a loved one. Not all the images have to be of people.

The site should not look like we practice law or that people can mistake us for attorneys.

Target Market(s)

People who just lost a loved one who had property, assets, in California but died with or without a will or trust. This is for people looking to hire non-attorneys.

Coding

Coded - Design and coding required

Font styles to use
Serif

Colors

Designer to choose colors to be used in the design.

Requirements
Must have
• Refer to Project Description.
Nice to have
• The sample images provided is what I am attracted to for the homepage image.
Should not have

```html
<!DOCTYPE html>
<html lang="en">
<head>
<meta charset="utf-8">
<title>The Velmar Hollow Group</title>
<link href="https://fonts.googleapis.com/css2?family=Mulish:wght@400;600;700&family=Open+Sans:wght@400;600;700&display=swap" rel="stylesheet">
<style>
:root{
  --blue:#0a6cbf;
  --blue-dark:#085ba3;
  --ink:#2b2b2b;
  --text:#444;
  --muted:#aaa;
  --panel:#ebebeb;
  --panel-light:#f3f3f3;
  --band-gray:#686868;
  --footer:#333;
  --white:#fff;
}
*{box-sizing:border-box;margin:0;padding:0}
html,body{width:1200px;height:2459px;overflow:hidden}
body{font-family:"Open Sans",sans-serif;color:var(--text);background:var(--white)}
.wrap{width:938px;margin:0 auto;position:relative}
.head-font{font-family:"Mulish",sans-serif}

/* header */
.site-header{height:102px}
.site-header .wrap{height:102px;display:flex;align-items:center;justify-content:space-between}
.brand{font-family:"Mulish",sans-serif;font-weight:700;font-size:38px;color:var(--blue);letter-spacing:-.3px;margin-top:-8px}
.header-phone{font-family:"Mulish",sans-serif;font-size:20px;color:var(--ink);display:flex;align-items:center;gap:8px;margin-top:-6px}

/* nav */
.main-nav{height:41px;background:var(--blue)}
.main-nav ul{list-style:none;display:flex;height:41px;width:938px;margin:0 auto}
.main-nav li{font-family:"Mulish",sans-serif;font-size:13px;font-weight:600;color:var(--white);display:flex;align-items:center;justify-content:center;height:41px}
.main-nav li.active{background:#333}

/* hero */
.hero{height:472px;position:relative;background:linear-gradient(180deg,#dfe9f2 0%,#c7d9e8 35%,#9fb3a8 55%,#86a85f 72%,#a7c27a 100%)}
.hero-copy{position:absolute;left:131px;top:66px}
.hero-copy p{font-size:17px;color:#222}
.hero-copy h1{font-family:"Mulish",sans-serif;font-size:24px;font-weight:700;color:#222;letter-spacing:.5px;margin-top:4px}
.hero-arrow{position:absolute;top:220px}

/* intro tabs */
.intro{padding-top:60px;height:750px;height:auto}
.tabs{display:flex;justify-content:center;gap:6px;margin-left:11px}
.tab{width:222px;height:51px;display:flex;align-items:center;justify-content:center;font-family:"Mulish",sans-serif;font-size:24px;position:relative}
.tab.active{background:var(--blue);color:var(--white)}
.tab.active::after{content:"";position:absolute;left:50%;bottom:-12px;margin-left:-11px;border-left:11px solid transparent;border-right:11px solid transparent;border-top:12px solid var(--blue)}
.tab.idle{background:var(--panel);color:var(--muted);border-bottom:4px solid var(--blue)}
.intro-text{font-size:12.5px;line-height:20.6px;text-align:center;color:#333;margin-top:24px}

/* steps */
.steps{margin-top:60px;height:392px;background:var(--blue);color:var(--white);text-align:center}
.steps h2{font-family:"Mulish",sans-serif;font-weight:600;font-size:32px;padding-top:58px}
.step-row{display:flex;justify-content:space-between;margin-top:30px}
.step{width:295px}
.step-icon{width:82px;height:82px;border:2px solid var(--white);border-radius:50%;margin:0 auto;display:flex;align-items:center;justify-content:center}
.step h3{font-family:"Mulish",sans-serif;font-weight:400;font-size:23px;margin-top:10px}
.step p{font-size:10.5px;line-height:15px;margin-top:4px}

/* price */
.price{height:341px;position:relative;background:linear-gradient(90deg,#cfcfcf 0%,#d8d8d6 45%,#e9e9e7 70%,#f1f1ef 100%)}
.price-photo{position:absolute;right:0;top:0;width:560px;height:341px;background:linear-gradient(90deg,rgba(230,230,228,0) 0%,#ecebe8 40%,#f4f3f0 100%)}
.price-copy{position:absolute;left:131px;top:70px;width:510px}
.price-copy h2{font-family:"Mulish",sans-serif;font-weight:600;font-size:31px;color:var(--blue)}
.price-copy p{font-size:17px;line-height:22px;color:#333;margin-top:6px}
.btn-row{display:flex;gap:11px;margin-top:20px}
.btn{background:var(--blue);color:var(--white);height:43px;display:flex;align-items:center;justify-content:center;gap:8px;border-radius:2px}
.btn.contact{width:141px;font-family:"Mulish",sans-serif;font-weight:700;font-size:15px}
.btn.phone{width:180px;font-family:"Mulish",sans-serif;font-size:19px}

/* faq */
.faq h2{font-family:"Mulish",sans-serif;font-weight:600;font-size:31px;color:var(--blue);text-align:center;padding-top:72px}
.faq-list{margin-top:32px}
.faq-item{margin-bottom:8px}
.faq-q{height:46px;background:var(--panel);display:flex;align-items:center;padding:0 14px;font-size:18px;color:#222}
.faq-q .q-icon{margin-right:12px;display:flex}
.faq-q .chev{margin-left:auto;display:flex}
.faq-a{background:var(--panel-light);padding:22px 48px 26px;font-size:11.5px;line-height:20px;color:#555}

/* contact band & footer */
.contact-band{position:absolute;top:2249px;left:0;width:1200px;height:80px;background:var(--band-gray);color:var(--white)}
.contact-band .wrap{height:80px;display:flex;align-items:center;justify-content:space-between;font-family:"Mulish",sans-serif;font-size:18px}
.contact-band span{display:flex;align-items:center;gap:9px}
.site-footer{position:absolute;top:2329px;left:0;width:1200px;height:130px;background:var(--footer);color:#ddd}
.footer-links{position:absolute;left:131px;top:40px;font-size:11px;display:flex;gap:9px;color:#ddd}
.copyright{position:absolute;left:131px;top:71px;font-size:11px;color:#ccc}
.social{position:absolute;right:131px;top:52px;display:flex;gap:9px}
.social span{width:24px;height:24px;border-radius:50%;background:#2f6fb4}
</style>
</head>
<body>

<header class="site-header">
  <div class="wrap">
    <div class="brand">The Velmar Hollow Group</div>
    <div class="header-phone">
      <svg width="16" height="16" viewBox="0 0 24 24"><path fill="#222" d="M6.6 10.8a15.1 15.1 0 0 0 6.6 6.6l2.2-2.2c.3-.3.7-.4 1-.2 1.1.4 2.3.6 3.6.6.6 0 1 .4 1 1V20c0 .6-.4 1-1 1A17 17 0 0 1 3 4c0-.6.4-1 1-1h3.5c.6 0 1 .4 1 1 0 1.3.2 2.5.6 3.6.1.3 0 .7-.2 1z"/></svg>
      555 014 7720
    </div>
  </div>
</header>

<nav class="main-nav">
  <ul>
    <li class="active" style="width:120px">HOME</li>
    <li style="width:137px">ABOUT</li>
    <li style="width:135px">PROBATE</li>
    <li style="width:150px">PROCESS</li>
    <li style="width:103px">FAQ</li>
    <li style="width:172px">CONTACT US</li>
    <li style="width:121px">BLOG</li>
  </ul>
</nav>

<section class="hero" role="img" aria-label="Photo of a young family walking hand in hand through a meadow of wildflowers under a bright sky">
  <div class="hero-copy">
    <p>Helping Californians deal with loss with</p>
    <h1>DIGNITY &amp; UNDERSTATING</h1>
  </div>
  <svg class="hero-arrow" style="left:46px" width="16" height="28" viewBox="0 0 16 28"><path d="M13 3 3 14l10 11" fill="none" stroke="#eee" stroke-width="3"/></svg>
  <svg class="hero-arrow" style="left:1136px" width="16" height="28" viewBox="0 0 16 28"><path d="m3 3 10 11L3 25" fill="none" stroke="#eee" stroke-width="3"/></svg>
</section>

<section class="intro">
  <div class="wrap">
    <div class="tabs">
      <div class="tab active">WHO WE ARE</div>
      <div class="tab idle">WHAT WE DO</div>
    </div>
    <p class="intro-text">We are not attorneys but legal document assistants who prepare legal documents for probate estate when someone dies with or without a will and assets need to be distributed. We have a flat-fee for Formal Probate of $999 and $699 for Informal Probate. We are an online company and offer our services to the entire state of California in every county. We do everything over the phone and email. The turn around time for us to prepare the initial legal paperwork for the client is within 3-5 business days. We can prepare, file, serve and manage a probate matter from petition to closing. We are not attorneys so our prices are very affordable compare to the attorney.</p>
  </div>
</section>

<section class="steps">
  <h2>Steps in Probate</h2>
  <div class="wrap step-row">
    <div class="step">
      <div class="step-icon">
        <svg width="34" height="34" viewBox="0 0 34 34" fill="none" stroke="#fff" stroke-width="2"><path d="M20 6H6v22h22V14"/><path d="M27 3l4 4-13 13-5 1 1-5z"/></svg>
      </div>
      <h3>Gather</h3>
      <p>We collect the will, asset records and family details needed to open the estate and prepare the petition.</p>
    </div>
    <div class="step">
      <div class="step-icon">
        <svg width="36" height="36" viewBox="0 0 36 36" fill="none" stroke="#fff" stroke-width="2"><circle cx="18" cy="18" r="5"/><circle cx="18" cy="18" r="11"/><path d="M18 3v4M18 29v4M3 18h4M29 18h4M7.4 7.4l2.8 2.8M25.8 25.8l2.8 2.8M7.4 28.6l2.8-2.8M25.8 10.2l2.8-2.8"/></svg>
      </div>
      <h3>Implement</h3>
      <p>We file, serve and track every document with the court so the estate moves forward without delays.</p>
    </div>
    <div class="step">
      <div class="step-icon">
        <svg width="34" height="36" viewBox="0 0 34 36" fill="none" stroke="#fff" stroke-width="2"><path d="M21 3H6v30h13"/><path d="M21 3l7 7v8"/><path d="M21 3v7h7"/><path d="M10 14h12M10 19h12M10 24h6"/><circle cx="25" cy="27" r="6"/><path d="m22 27 2 2 4-4"/></svg>
      </div>
      <h3>Close</h3>
      <p>Once assets are settled we prepare the final accounting and closing papers so heirs receive their share.</p>
    </div>
  </div>
</section>

<section class="price">
  <div class="price-photo" role="img" aria-label="Photo of a hand signing a document with a fountain pen"></div>
  <div class="price-copy">
    <h2>Flat-Fee Price &amp; Savings</h2>
    <p>Etiam mattis augue vehicula odio posuere, sit amet tempus lectus luctus. Nulla facilisi. Etiam vel massa elementum, bibendum tellus venenatis, feugiat massa. Curabitur venenatis lacinia ornare.</p>
    <div class="btn-row">
      <div class="btn contact">CONTACT US</div>
      <div class="btn phone">
        <svg width="15" height="15" viewBox="0 0 24 24"><path fill="#fff" d="M6.6 10.8a15.1 15.1 0 0 0 6.6 6.6l2.2-2.2c.3-.3.7-.4 1-.2 1.1.4 2.3.6 3.6.6.6 0 1 .4 1 1V20c0 .6-.4 1-1 1A17 17 0 0 1 3 4c0-.6.4-1 1-1h3.5c.6 0 1 .4 1 1 0 1.3.2 2.5.6 3.6.1.3 0 .7-.2 1z"/></svg>
        555 014 7720
      </div>
    </div>
  </div>
</section>

<section class="faq">
  <h2>You Have Questions? We Have Answers...</h2>
  <div class="wrap faq-list">
    <div class="faq-item">
      <div class="faq-q"><span class="q-icon"><svg width="16" height="16" viewBox="0 0 16 16"><circle cx="8" cy="8" r="8" fill="#222"/><path d="M5.8 6a2.2 2.2 0 1 1 3 2c-.6.3-.8.6-.8 1.2v.4" fill="none" stroke="#ebebeb" stroke-width="1.6"/><circle cx="8" cy="12" r="1" fill="#ebebeb"/></svg></span>Pellentesque convallis molestie enim sit amet efficitur?<span class="chev"><svg width="12" height="8" viewBox="0 0 12 8"><path d="m1 1 5 5 5-5" fill="none" stroke="#333" stroke-width="1.6"/></svg></span></div>
      <div class="faq-a">Most estates in California need a court petition when the assets exceed the small estate limit. We review your situation by phone, explain whether formal or informal probate fits best, and prepare the initial paperwork within three to five business days. You stay informed by email at every step, and our flat fee covers document preparation from petition to closing with no hourly billing.</div>
    </div>
    <div class="faq-item">
      <div class="faq-q"><span class="q-icon"><svg width="16" height="16" viewBox="0 0 16 16"><circle cx="8" cy="8" r="8" fill="#222"/><path d="M5.8 6a2.2 2.2 0 1 1 3 2c-.6.3-.8.6-.8 1.2v.4" fill="none" stroke="#ebebeb" stroke-width="1.6"/><circle cx="8" cy="12" r="1" fill="#ebebeb"/></svg></span>Nunc sit amet consequat risus?<span class="chev"><svg width="12" height="8" viewBox="0 0 12 8"><path d="m1 1 5 5 5-5" fill="none" stroke="#333" stroke-width="1.6"/></svg></span></div>
    </div>
    <div class="faq-item">
      <div class="faq-q"><span class="q-icon"><svg width="16" height="16" viewBox="0 0 16 16"><circle cx="8" cy="8" r="8" fill="#222"/><path d="M5.8 6a2.2 2.2 0 1 1 3 2c-.6.3-.8.6-.8 1.2v.4" fill="none" stroke="#ebebeb" stroke-width="1.6"/><circle cx="8" cy="12" r="1" fill="#ebebeb"/></svg></span>Curabitur ac elit leo in eleifend dui tellus in scelerisque elit porttitor?<span class="chev"><svg width="12" height="8" viewBox="0 0 12 8"><path d="m1 1 5 5 5-5" fill="none" stroke="#333" stroke-width="1.6"/></svg></span></div>
    </div>
    <div class="faq-item">
      <div class="faq-q"><span class="q-icon"><svg width="16" height="16" viewBox="0 0 16 16"><circle cx="8" cy="8" r="8" fill="#222"/><path d="M5.8 6a2.2 2.2 0 1 1 3 2c-.6.3-.8.6-.8 1.2v.4" fill="none" stroke="#ebebeb" stroke-width="1.6"/><circle cx="8" cy="12" r="1" fill="#ebebeb"/></svg></span>Integer eu massa lacinia lacinia nulla non volutpat purus?<span class="chev"><svg width="12" height="8" viewBox="0 0 12 8"><path d="m1 1 5 5 5-5" fill="none" stroke="#333" stroke-width="1.6"/></svg></span></div>
    </div>
    <div class="faq-item">
      <div class="faq-q"><span class="q-icon"><svg width="16" height="16" viewBox="0 0 16 16"><circle cx="8" cy="8" r="8" fill="#222"/><path d="M5.8 6a2.2 2.2 0 1 1 3 2c-.6.3-.8.6-.8 1.2v.4" fill="none" stroke="#ebebeb" stroke-width="1.6"/><circle cx="8" cy="12" r="1" fill="#ebebeb"/></svg></span>Aenean sed quam non sapien faucibus consequat vitae?<span class="chev"><svg width="12" height="8" viewBox="0 0 12 8"><path d="m1 1 5 5 5-5" fill="none" stroke="#333" stroke-width="1.6"/></svg></span></div>
    </div>
  </div>
</section>

<section class="contact-band">
  <div class="wrap">
    <span><svg width="12" height="17" viewBox="0 0 12 17"><path fill="#fff" d="M6 0a6 6 0 0 0-6 6c0 4.5 6 11 6 11s6-6.5 6-11a6 6 0 0 0-6-6zm0 8.2A2.2 2.2 0 1 1 6 3.8a2.2 2.2 0 0 1 0 4.4z"/></svg>24 Building name, Street name, City - Zipcode</span>
    <span><svg width="15" height="15" viewBox="0 0 24 24"><path fill="#fff" d="M6.6 10.8a15.1 15.1 0 0 0 6.6 6.6l2.2-2.2c.3-.3.7-.4 1-.2 1.1.4 2.3.6 3.6.6.6 0 1 .4 1 1V20c0 .6-.4 1-1 1A17 17 0 0 1 3 4c0-.6.4-1 1-1h3.5c.6 0 1 .4 1 1 0 1.3.2 2.5.6 3.6.1.3 0 .7-.2 1z"/></svg>555 014 7721</span>
    <span><svg width="17" height="13" viewBox="0 0 17 13"><rect width="17" height="13" rx="1.5" fill="#fff"/><path d="m1 1.5 7.5 6 7.5-6" fill="none" stroke="#686868" stroke-width="1.4"/></svg>info@velmarhollow.com</span>
  </div>
</section>

<footer class="site-footer">
  <div class="footer-links"><span>Home</span>|<span>About</span>|<span>Probate</span>|<span>Process</span>|<span>FAQ</span>|<span>Contact Us</span>|<span>Blog</span></div>
  <div class="copyright">Copyright &copy; 2017 &nbsp;The Velmar Hollow Group. &nbsp;All rights reserved.</div>
  <div class="social"><span></span><span></span><span></span></div>
</footer>

</body>
</html>
```